Vodka Bottle Label - Luma Vodka

I need a bottle label for a vodka I'd like to make called Luma Vodka.
I would like a label that looks elegant and fresh. I would like some mountains and colours to be red and white. Open to other colours being added but not too colourful. "Luma" means fresh, dawn in polish, i would like if mountains or something extra was added to the label too. I would like the Luma Vodka name not to be too small.
The vodka is made in australia and is 37%.

I would love to have a little bit of gold colour in the label!

I will provide the back label words when completing my decision.

i'd like to make it more simple and less european looking. More australian.

I saw a bottle like this and i did like the concept.

https://www.tallgumcellars.com.au/spirits/qrnt-vodka-range?srsltid=ZtqWXkelmaHuP31-ra-m7s92xudhfew_pT8eWnGBbRTxLsb3hTyQsdGaqYt

Target Market(s)

Vodka Drinkers

Industry/Entity Type

Alcohol

Colors
EB3D1F
EC4F4E
F09395
F8D3D4
FCEDEE

Requirements
Must have
• red and white colours incorporated, mountains or freshness on it.
Nice to have
• Fresh and clean look. Classy

```html
<!DOCTYPE html>
<html lang="en">
<head>
<meta charset="utf-8">
<title>Luma Vodka – Bottle Labels</title>
<link rel="stylesheet" href="https://fonts.googleapis.com/css2?family=Playfair+Display:wght@400;700&family=Oswald:wght@500&family=Montserrat:wght@700&family=Open+Sans:wght@600&family=Great+Vibes&display=swap">
<style>
  :root {
    --ink: #000000;
    --red: #e3342f;
    --red-deep: #c41f24;
    --red-dark: #9e1a1d;
    --rose: #f09395;
    --blush: #f8d3d4;
    --paper: #f4f3f3;
    --white: #ffffff;
    --gold: #e8b52b;
    --gold-light: #fbe08a;
    --gold-dark: #c88b1d;
    --text-dark: #1d1d1d;
  }
  html, body {
    margin: 0;
    padding: 0;
    width: 1200px;
    height: 1200px;
    overflow: hidden;
    background: var(--ink);
  }
  .labels { display: block; width: 1200px; height: 1200px; }
  .serif { font-family: "Playfair Display", "Bodoni Moda", serif; }
  .condensed { font-family: "Oswald", "Arial Narrow", sans-serif; font-weight: 500; }
  .sans-bold { font-family: "Montserrat", Arial, sans-serif; font-weight: 700; }
  .body-copy { font-family: "Open Sans", Arial, sans-serif; font-weight: 600; font-size: 17px; fill: var(--text-dark); }
  .script { font-family: "Great Vibes", cursive; }
</style>
</head>
<body>
<svg class="labels" viewBox="0 0 1932 1932" xmlns="http://www.w3.org/2000/svg">
  <defs>
    <linearGradient id="gold" x1="0" y1="0" x2="1" y2="1">
      <stop offset="0" stop-color="var(--gold-dark)"/>
      <stop offset="0.3" stop-color="var(--gold-light)"/>
      <stop offset="0.55" stop-color="var(--gold)"/>
      <stop offset="0.8" stop-color="var(--gold-light)"/>
      <stop offset="1" stop-color="var(--gold-dark)"/>
    </linearGradient>
    <linearGradient id="goldLine" x1="0" y1="0" x2="1" y2="0">
      <stop offset="0" stop-color="var(--gold-dark)"/>
      <stop offset="0.5" stop-color="var(--gold-light)"/>
      <stop offset="1" stop-color="var(--gold-dark)"/>
    </linearGradient>
    <linearGradient id="bandRed" x1="0" y1="0" x2="0" y2="1">
      <stop offset="0" stop-color="var(--red)"/>
      <stop offset="1" stop-color="var(--red-deep)"/>
    </linearGradient>
    <linearGradient id="bandSide" x1="0" y1="0" x2="1" y2="0">
      <stop offset="0" stop-color="var(--red-deep)"/>
      <stop offset="1" stop-color="var(--red-dark)"/>
    </linearGradient>
    <linearGradient id="mountains" x1="0" y1="0" x2="0" y2="1">
      <stop offset="0" stop-color="var(--rose)" stop-opacity="0.2"/>
      <stop offset="0.5" stop-color="#d67274"/>
      <stop offset="1" stop-color="#a8383b"/>
    </linearGradient>
    <linearGradient id="paper" x1="0" y1="0" x2="1" y2="1">
      <stop offset="0" stop-color="var(--white)"/>
      <stop offset="0.5" stop-color="#fbf2f2"/>
      <stop offset="1" stop-color="#ececec"/>
    </linearGradient>
    <radialGradient id="sealCore" cx="0.4" cy="0.35" r="0.7">
      <stop offset="0" stop-color="var(--white)"/>
      <stop offset="1" stop-color="#c9cbd3"/>
    </radialGradient>
    <path id="frontShape" d="M220,530 Q290,530 300,450 C340,390 430,348 527,348 C624,348 714,390 755,450 Q765,530 835,530 V1400 Q765,1400 755,1480 C714,1542 624,1582 527,1582 C430,1582 340,1542 300,1480 Q290,1400 220,1400 Z"/>
    <path id="backShape" d="M1097,490 Q1097,435 1145,435 Q1150,348 1220,348 H1590 Q1660,348 1665,435 Q1712,435 1712,490 V1440 Q1712,1495 1665,1495 Q1660,1582 1590,1582 H1220 Q1150,1582 1145,1495 Q1097,1495 1097,1440 Z"/>
    <polygon id="star" points="0,-13 3.8,-4 13,-4 5.6,2 8.4,12 0,6 -8.4,12 -5.6,2 -13,-4 -3.8,-4"/>
  </defs>

  <!-- Front label -->
  <g class="front-label">
    <use href="#frontShape" fill="url(#gold)"/>
    <use href="#frontShape" fill="var(--paper)" transform="translate(527.5 965) scale(0.935 0.965) translate(-527.5 -965)"/>
    <use href="#frontShape" fill="var(--red)" transform="translate(527.5 965) scale(0.862 0.92) translate(-527.5 -965)"/>
    <use href="#frontShape" fill="url(#paper)" transform="translate(527.5 965) scale(0.772 0.882) translate(-527.5 -965)"/>

    <rect class="grape-emblem" x="478" y="510" width="97" height="150" rx="40" fill="var(--red)" opacity="0.85" role="img" aria-label="Grape cluster emblem"/>

    <rect class="premium-tag" x="433" y="685" width="188" height="29" rx="3" fill="var(--red)"/>
    <text class="condensed" x="527" y="708" font-size="23" fill="var(--white)" text-anchor="middle">PREMIUM PRODUCT</text>

    <rect class="band-side" x="220" y="775" width="615" height="410" fill="url(#bandSide)"/>
    <rect class="band-panel" x="262" y="775" width="530" height="400" fill="url(#bandRed)"/>
    <rect class="mountain-scene" x="262" y="1050" width="530" height="122" fill="url(#mountains)" role="img" aria-label="Sketched mountain range with setting sun and birds"/>

    <g class="rating" fill="var(--white)">
      <use href="#star" x="435" y="852" transform="scale(1)"/>
      <use href="#star" x="475" y="848"/>
      <use href="#star" x="580" y="848"/>
      <use href="#star" x="620" y="852"/>
      <rect x="499" y="818" width="58" height="42" rx="4" role="img" aria-label="Crown emblem"/>
    </g>

    <text class="serif brand-name" x="527" y="938" font-size="84" fill="var(--white)" text-anchor="middle" textLength="450" lengthAdjust="spacingAndGlyphs">LUMA VODKA</text>

    <rect class="origin-tag" x="345" y="967" width="358" height="29" rx="2" fill="var(--white)"/>
    <text class="sans-bold" x="524" y="989" font-size="19" fill="var(--red)" text-anchor="middle" letter-spacing="7">MADE IN AUSTRALIA</text>

    <g class="since-seal">
      <circle cx="527" cy="1295" r="98" fill="#d9dade"/>
      <circle cx="527" cy="1295" r="90" fill="var(--red)"/>
      <circle cx="527" cy="1295" r="60" fill="url(#sealCore)"/>
      <circle cx="527" cy="1295" r="54" fill="none" stroke="var(--red-dark)" stroke-width="2" stroke-dasharray="6 4"/>
      <g fill="#e4e5ea">
        <use href="#star" x="503" y="1222" transform="scale(1)"/>
        <use href="#star" x="527" y="1220"/>
        <use href="#star" x="551" y="1222"/>
      </g>
      <circle cx="527" cy="1374" r="6" fill="var(--white)"/>
      <text class="condensed" x="527" y="1287" font-size="30" fill="var(--red)" text-anchor="middle">since</text>
      <text class="condensed" x="527" y="1327" font-size="40" fill="var(--red)" text-anchor="middle">1990</text>
    </g>

    <text class="condensed" x="527" y="1443" font-size="30" fill="var(--red)" text-anchor="middle">ALC 40%</text>
    <text class="condensed" x="527" y="1480" font-size="30" fill="var(--red)" text-anchor="middle">750ML</text>
  </g>

  <!-- Back label -->
  <g class="back-label">
    <use href="#backShape" fill="url(#gold)"/>
    <use href="#backShape" fill="var(--red)" transform="translate(1404.5 965) scale(0.968 0.982) translate(-1404.5 -965)"/>
    <use href="#backShape" fill="url(#paper)" transform="translate(1404.5 965) scale(0.945 0.968) translate(-1404.5 -965)"/>

    <g class="rating" fill="var(--red)">
      <use href="#star" x="1314" y="445"/>
      <use href="#star" x="1352" y="442"/>
      <use href="#star" x="1458" y="442"/>
      <use href="#star" x="1496" y="445"/>
      <rect x="1377" y="410" width="56" height="43" rx="4" role="img" aria-label="Crown emblem"/>
    </g>
    <text class="sans-bold" x="1405" y="515" font-size="27" fill="var(--red)" text-anchor="middle">SINCE-1990</text>

    <rect class="band" x="1097" y="558" width="615" height="404" fill="url(#bandRed)"/>
    <rect x="1097" y="570" width="615" height="12" fill="url(#goldLine)"/>
    <rect x="1097" y="938" width="615" height="12" fill="url(#goldLine)"/>
    <rect class="mountain-scene" x="1097" y="805" width="615" height="133" fill="url(#mountains)" role="img" aria-label="Sketched mountain range with setting sun and birds"/>

    <text class="serif" x="1405" y="712" font-size="124" font-weight="700" fill="var(--white)" text-anchor="middle" textLength="520" lengthAdjust="spacingAndGlyphs">VODKA</text>
    <text class="script" x="1405" y="765" font-size="42" fill="var(--white)" text-anchor="middle">Authentic Australian Recipe</text>

    <text class="condensed" x="1405" y="1078" font-size="42" fill="var(--red)" text-anchor="middle">PREMIUM PRODUCT</text>

    <g class="body-copy" text-anchor="middle">
      <text x="1405" y="1128">Lorem Ipsum Dolor Sit Amet,</text>
      <text x="1405" y="1152">Consectetuer Adipiscing Elit,</text>
      <text x="1405" y="1176">Sed Diam Nonummy Nibh</text>
      <text x="1405" y="1200">Euismod Tincidunt Ut Laoreet</text>
      <text x="1405" y="1224">Dolore Magna Aliquam Erat</text>
      <text x="1405" y="1248">Volutpat. Ut Wisi Enim Ad</text>
      <text x="1398" y="1296">Lorem ipsum dolor sit amet,</text>
      <text x="1398" y="1320">consectetuer adipiscing elit,</text>
      <text x="1398" y="1344">sed diam nonummy nibh</text>
      <text x="1398" y="1368">euismod tincidunt ut laoreet</text>
      <text x="1398" y="1392">dolore magna aliquam erat</text>
      <text x="1398" y="1416">volutpat. Ut wisi enim ad</text>
      <text x="1398" y="1440">minim</text>
    </g>

    <g class="spec-row">
      <text class="condensed" x="1235" y="1510" font-size="28" fill="var(--red)" text-anchor="middle">ALC</text>
      <text class="condensed" x="1235" y="1540" font-size="28" fill="var(--red)" text-anchor="middle">40%</text>
      <rect x="1288" y="1487" width="5" height="58" fill="var(--red)"/>
      <text class="serif" x="1405" y="1525" font-size="25" fill="var(--red)" text-anchor="middle">ALL-NATURAL</text>
      <rect x="1518" y="1487" width="5" height="58" fill="var(--red)"/>
      <text class="condensed" x="1565" y="1510" font-size="28" fill="var(--red)" text-anchor="middle">750</text>
      <text class="condensed" x="1562" y="1540" font-size="28" fill="var(--red)" text-anchor="middle">ML</text>
    </g>
  </g>
</svg>
</body>
</html>
```